Ridgeline Journeys business card

please see website
www.ridgelinejourneys.comau

info needed on card
Curtis Halvey
Ph
email
Adventure Riding GPS trails

please use my logo and colours off my site

Curtis Halvey
curtis@ridgelinejourneys.com

```html
<!DOCTYPE html>
<html lang="en">
<head>
<meta charset="utf-8">
<title>Ridgeline Journeys business card</title>
<link rel="stylesheet" href="https://fonts.googleapis.com/css2?family=Source+Sans+3:ital,wght@0,400;0,600;0,700;0,800;1,600&display=swap">
<style>
  :root {
    --stage: #000000;
    --card-light: #f3f3f3;
    --brand-yellow: #ffd20a;
    --ink: #111111;
    --name-yellow: #f7c81e;
    --white: #ffffff;
  }
  * { margin: 0; padding: 0; box-sizing: border-box; }
  html, body {
    width: 1200px; height: 900px; overflow: hidden;
    background: var(--stage);
    font-family: "Source Sans 3", "Myriad Pro", Arial, sans-serif;
  }
  .canvas { position: relative; width: 1200px; height: 900px; }

  .card { position: absolute; top: 200px; width: 310px; height: 502px; }

  .card-front {
    left: 265px;
    background: var(--card-light);
    border-radius: 50px 0 52px 0;
  }
  .brand-lockup {
    position: absolute; left: 38px; top: 50px;
    display: flex; align-items: center; gap: 16px;
  }
  .brand-mark {
    width: 46px; height: 46px; background: var(--brand-yellow);
  }
  .brand-name {
    font-weight: 800; font-size: 27px; line-height: 1;
    color: var(--ink); text-transform: uppercase; letter-spacing: 0.2px;
  }
  .tagline {
    position: absolute; left: 0; right: 0; top: 143px;
    text-align: center; font-style: italic; font-weight: 600;
    font-size: 17px; color: var(--ink); padding-left: 30px;
  }
  .holder-name {
    position: absolute; left: 25px; top: 342px;
    font-weight: 700; font-size: 17px; color: var(--name-yellow);
  }
  .contact-list {
    position: absolute; left: 25px; top: 386px; list-style: none;
  }
  .contact-item {
    display: flex; align-items: center; gap: 7px;
    font-size: 14px; color: var(--ink); height: 21px;
  }
  .contact-icon { width: 13px; height: 13px; flex: none; }

  .card-back {
    left: 641px;
    background: var(--brand-yellow);
    border-radius: 0 55px 0 55px;
  }
  .back-name {
    position: absolute; left: 0; right: 0; top: 356px;
    text-align: center; color: var(--white);
    font-weight: 800; font-size: 38px; line-height: 1.05;
    text-transform: uppercase; padding-left: 22px;
  }
</style>
</head>
<body>
<main class="canvas">
  <section class="card card-front" aria-label="Business card front">
    <div class="brand-lockup">
      <span class="brand-mark"></span>
      <span class="brand-name">Ridgeline<br>Journeys</span>
    </div>
    <p class="tagline">Adventure Riding GPS trails</p>

    <p class="holder-name">Curtis Halvey</p>
    <ul class="contact-list">
      <li class="contact-item">
        <svg class="contact-icon" viewBox="0 0 13 13" aria-hidden="true">
          <rect width="13" height="13" rx="2" fill="#ffd20a"/>
          <path d="M3 4.5h7v1.3H3z M3.5 6.3h6l0.8 3.2H2.7z" fill="#111"/>
        </svg>
        <span>(044)-318-2094</span>
      </li>
      <li class="contact-item">
        <svg class="contact-icon" viewBox="0 0 13 13" aria-hidden="true">
          <rect width="13" height="13" rx="2" fill="#ffd20a"/>
          <rect x="2.5" y="3.8" width="8" height="5.4" fill="#111"/>
          <path d="M2.5 3.8l4 3 4-3" stroke="#ffd20a" stroke-width="0.8" fill="none"/>
        </svg>
        <span>curtis@ridgelinejourneys.com</span>
      </li>
      <li class="contact-item">
        <svg class="contact-icon" viewBox="0 0 13 13" aria-hidden="true">
          <rect width="13" height="13" rx="2" fill="#ffd20a"/>
          <path d="M4.2 8.8l4.6-4.6 M3.6 7.2l-0.8 0.8a1.4 1.4 0 0 0 2 2l0.8-0.8 M7.2 3.6l0.8-0.8a1.4 1.4 0 0 1 2 2l-0.8 0.8" stroke="#111" stroke-width="1.1" fill="none" stroke-linecap="round"/>
        </svg>
        <span>www.ridgelinejourneys.com</span>
      </li>
    </ul>
  </section>

  <section class="card card-back" aria-label="Business card back">
    <p class="back-name">Ridgeline<br>Journeys</p>
  </section>
</main>
</body>
</html>
```